Government contracting small business needs a web design

Tarvex Summit Inc is a veteran owned small business that delivers a full range of professional services as well as training in information technology, security and defense intelligence solutions.
We need a professional/corporate looking website where potential clients can view what services are offered.
This being a new company, there is not much that can added more than a narrative statement, stock photos and a place where potential customers and employees can make contact.
Open to ideas.
Target Market(s)
US Government
Industry/Entity Type
Small Business
Look and feel
Each slider illustrates characteristics of the customer's brand and the style your logo design should communicate.

```html
<!DOCTYPE html>
<html lang="en">
<head>
<meta charset="utf-8">
<title>Tarvex Summit Inc</title>
<link href="https://fonts.googleapis.com/css2?family=Arimo:ital,wght@0,400;0,700;1,700&display=swap" rel="stylesheet">
<style>
:root{
  --orange:#ff7a00;
  --orange-deep:#f26a00;
  --ink:#222;
  --text:#333;
  --nav:#555;
  --muted:#777;
  --rule:#9a9a9a;
  --hero-dark:#2e2e2e;
  --hero-mid:#5b5b5b;
  --white:#fff;
}
*{margin:0;padding:0;box-sizing:border-box}
html,body{width:963px;height:1200px;overflow:hidden;background:var(--white)}
body{position:relative;font-family:"Arimo",Arial,sans-serif;color:var(--text)}
.abs{position:absolute}
.brand{left:52px;top:36px;display:flex;align-items:center;gap:14px}
.brand-name{font-size:60px;font-weight:700;letter-spacing:-3px;color:#444;line-height:1}
.brand-dot{width:64px;height:64px;border-radius:50%;background:var(--orange)}
.contact{top:28px;font-size:9.5px;line-height:20px;color:var(--muted)}
.contact.addr{left:623px}
.contact.reach{left:723px;color:var(--orange)}
.main-nav{top:95px;left:0;font-size:15px;font-weight:700;color:var(--nav)}
.main-nav span{position:absolute;white-space:nowrap}
.top-rule{left:11px;top:120px;width:940px;height:3px;background:var(--orange)}
.hero{left:11px;top:123px;width:940px;height:584px;
  background:linear-gradient(180deg,#3a3a3a 0%,#4a4a4a 45%,#8a8a8a 70%,#4d4d4d 88%,#222 100%)}
.slide{left:151px;top:217px;width:659px;height:270px;
  background:linear-gradient(135deg,#6b625a 0%,#3c4a5a 40%,#8a7a66 70%,#2f2a26 100%)}
.slide-tag{right:163px;top:376px;background:rgba(0,0,0,.75);color:var(--orange);font-weight:700;font-size:15px;padding:2px 8px}
.slide-title{right:153px;top:398px;background:rgba(0,0,0,.85);color:var(--white);font-weight:700;font-size:19px;padding:2px 8px}
.slide-bar{left:151px;top:487px;width:659px;height:40px;background:rgba(20,20,20,.85);display:flex;justify-content:center;align-items:center;gap:4.5px}
.slide-bar i{width:12px;height:12px;border-radius:50%;background:#eee;display:block}
.slide-bar i.on{background:var(--orange-deep)}
.card{top:655px;width:209px;height:78px;background:var(--white);box-shadow:0 2px 4px rgba(0,0,0,.35)}
.card svg{position:absolute;left:10px;top:14px}
.card-title{position:absolute;right:15px;top:20px;font-size:15px;font-weight:700;color:var(--ink)}
.card-link{position:absolute;right:15px;top:53px;font-size:10.5px;font-weight:700;color:var(--orange)}
.about-title{left:160px;top:764px;font-size:17px;font-weight:700;font-style:italic;color:var(--orange)}
.about-text{left:160px;top:792px;width:640px;font-size:12.5px;line-height:14.7px;color:var(--ink)}
.rule{left:152px;width:661px;height:1px;background:var(--rule)}
.col{top:932px}
.col h3{font-size:14px;font-weight:400;color:var(--orange);margin:0 0 10px 3px}
.col ul{list-style:none;font-size:12.5px;line-height:14.6px;color:var(--ink)}
.copy{left:160px;top:1094px;font-size:11.5px;line-height:14.5px;color:var(--muted)}
.foot-nav{top:1094px;left:0;font-size:12.5px;color:var(--ink)}
.foot-nav span{position:absolute;white-space:nowrap}
</style>
</head>
<body>
<header>
  <div class="abs brand"><span class="brand-name">Tarvex</span><span class="brand-dot"></span></div>
  <div class="abs contact addr">42 Ridgeline Way, 210<br>Halden, CO 80999</div>
  <div class="abs contact reach">(+00) 5550 14 207<br>hello@tarvexsummit.com</div>
  <nav class="abs main-nav">
    <span style="left:362px">Home</span><span style="left:440px">Company</span><span style="left:540px">Services</span><span style="left:625px">Projects</span><span style="left:712px">Contact Us</span>
  </nav>
  <div class="abs top-rule"></div>
</header>

<section>
  <div class="abs hero" role="img" aria-label="Night view of a domed government capitol building lit by street lamps"></div>
  <div class="abs slide" role="img" aria-label="Operators working in a security operations center with many monitors"></div>
  <div class="abs slide-tag">/ INFRASTRUCTURE /</div>
  <div class="abs slide-title">Cyber Security Solutions</div>
  <div class="abs slide-bar"><i class="on"></i><i></i><i></i><i></i><i></i><i></i></div>

  <div class="abs card" style="left:152px">
    <svg width="30" height="30" viewBox="0 0 30 30"><circle cx="14" cy="14" r="12" fill="#888"/><ellipse cx="14" cy="14" rx="5" ry="12" fill="none" stroke="#ddd"/><line x1="2" y1="14" x2="26" y2="14" stroke="#ddd"/><rect x="16" y="18" width="10" height="9" fill="#bbb"/></svg>
    <span class="card-title">Cyber Security</span><span class="card-link">LEARN MORE</span>
  </div>
  <div class="abs card" style="left:377px">
    <svg width="32" height="28" viewBox="0 0 32 28"><rect x="1" y="8" width="8" height="18" fill="#777"/><rect x="11" y="4" width="9" height="22" fill="#999"/><rect x="22" y="1" width="9" height="25" fill="#666"/></svg>
    <span class="card-title">Dynamic Data Center</span><span class="card-link">LEARN MORE</span>
  </div>
  <div class="abs card" style="left:602px">
    <svg width="32" height="30" viewBox="0 0 32 30"><rect x="1" y="2" width="28" height="19" fill="#777"/><rect x="4" y="5" width="22" height="13" fill="#cfd6dc"/><rect x="12" y="21" width="6" height="4" fill="#888"/><rect x="7" y="25" width="16" height="3" fill="#999"/></svg>
    <span class="card-title">Full Motion Video</span><span class="card-link">LEARN MORE</span>
  </div>
</section>

<section>
  <h2 class="abs about-title">/ ABOUT US /</h2>
  <p class="abs about-text">Tarvex Summit® is one of the fastest growing information technology solutions providers in the country. Founded in 1997, the veteran-owned, privately held business has consistently grown both its revenue and its staff since the company’s inception.<br>Based in Ridgeford, CO, Tarvex also has an office in Ashcombe, VA, that houses its federal operations. Today, Tarvex is approximately 100 employees strong, with its seasoned professionals possessing decades of experience – working in the public and private sectors – as well as top-secret security clearances.</p>
</section>

<footer>
  <div class="abs rule" style="top:905px"></div>
  <div class="abs col" style="left:165px"><h3>Company</h3><ul><li>Executive Team</li><li>Corporate Values</li><li>Certifications</li><li>Clients and Partners</li><li>Government Contracting</li><li>Contact Us</li><li>Careers</li></ul></div>
  <div class="abs col" style="left:349px"><h3>Solution Center</h3><ul><li>BPM</li><li>Cyber Security</li><li>DR/COOP</li><li>Dynamic Data Center</li><li>Full Motion Video</li><li>Mobility Solutions</li><li>Virtualization</li></ul></div>
  <div class="abs col" style="left:512px"><h3>Press and News</h3><ul><li>Case Studies</li><li>Press releases</li><li>Events</li></ul></div>
  <div class="abs col" style="left:679px"><h3>Clients &amp; Partners</h3><ul><li>Clients</li><li>Integrator Partners</li><li>Partner Alliances</li></ul></div>
  <div class="abs rule" style="top:1085px"></div>
  <div class="abs copy">2012 - Tarvex Summit Incorporated.<br>All rights reserved.</div>
  <nav class="abs foot-nav">
    <span style="left:459px">Home</span><span style="left:525px">Company</span><span style="left:608px">Services</span><span style="left:679px">Projects</span><span style="left:750px">Contact Us</span>
  </nav>
</footer>
</body>
</html>
```